WE ARE BRIGHT SPARROW, building a full website with ecommerce

requirements:
CODED FOR SITEQUILL
ONLINE STORE FUNCTION WITH E-COMMERCE USING TRADEBLOOM
PAGEWAVE AND PICTOLANE LINKS

I need a website design for my organization, WE ARE BRIGHT SPARROW, a global empowerment movement elevating woman, and the world. The site's home page should reflect our mission, to empower women. It should have a strong, empowering feel, with minimalistic design.
Please see www.lunavelto.com and http://www.corvenhal.co/ for an inspiration on layout and feel.

**PLEASE SEE ATTACHMENT "LOGO MOCK UP" FOR LOGO. THIS IS NOT THE FINAL VECTOR FILE, BUT THIS LOOKS THE SAME AS THE FINAL LOGO.

HOME PAGE:
The first section of the home page should include a background image with our logo center.

You should include the following links to pages at the top right of the page:
MISSION
MANTRA
ARMOR
MEET BS (I would like "bs" to be our logo)
pagewave and pictolane links

As you scroll down the page, you should see the following sections, which correlate to the links to pages as written above. **SEE ATTACHED SKETCH "HOMEPAGE LAYOUT IDEA" FOR REFERENCE**

WHO WE ARE (correlates to the link Mission)

OUR MANTRA (correlates to the link Mantra)

OUR ARMOR (correlates to the link The Shirt)
(This is where we will sell a shirt (and other apparel) and need the e-commerce function)

MEET BRIGHT SPARROWS (correlates to the link Meet BS)

SHOW OFF YOUR SUPER POWERS (correlates to the pagewave and pictolane)

FEATURED BRIGHT SPARROW (no link on top right of page)

On the homepage, for each of the above sections, as you scroll down there should be an image, either in the background or framed, next to the title (WHO WE ARE, for example), as well as one sentence of small text explaining the title. The title (WHO WE ARE) and the one sentence should link to a page (ie WHO WE ARE + the one sentence links to the MISSION page). ** SEE ATTACHED SKETCH "HOMEPAGE SECTION IDEAS" FOR REFERENCE**

**PLEASE SEE ATTACHMENT "WEBSITE TITLE IDEAS" FOR A STARTING PLACE OF THE LOOK. These don't have to be exact, but they give you an idea of what I'm looking for.

**FONTS TYPOLD EXTRA BOLD AND TYPOLD BOOK 500 (WHICH SHOULD BE BOLDED MANUALLY) ARE ATTACHED**

Target Market(s)

Women, mainly in US

Industry/Entity Type

Social

Coding

Coded - Design and coding required

Number of Pages Required

5+ page

Font styles to use
Other font styles liked:
• Typol Extra Bold

Requirements
Must have
• CODED FOR SITEQUILL
• ONLINE STORE FUNCTION WITH E-COMMERCE USING TRADEBLOOM
• PAGEWAVE AND PICTOLANE LINKS
• Typold Extra Bold and Typold Book 500, attached
• please see description for all requirements
Nice to have
• please see description for all ideas
Should not have

```html
<!DOCTYPE html>
<html lang="en">
<head>
<meta charset="UTF-8">
<title>We Are Bright Sparrow</title>
<link rel="stylesheet" href="https://fonts.googleapis.com/css2?family=Montserrat:wght@400;500;700;800&display=swap">
<style>
:root{
  --ink:#111111;
  --white:#ffffff;
  --soft:#f0f0f0;
  --muted:#8a8a8a;
  --body:#6f6f6f;
  --hero-top:#c9bfb2;
  --hero-bottom:#5a4a3e;
  --who-a:#e8c48a;
  --who-b:#8a6a4e;
  --mantra-a:#4e3b52;
  --mantra-b:#9a7f88;
  --meet-a:#3d3834;
  --meet-b:#6e625a;
}
*{box-sizing:border-box;margin:0;padding:0}
html,body{width:1200px;height:4018px;overflow:hidden}
body{font-family:"Montserrat",sans-serif;color:var(--ink);background:var(--white);position:relative}
.section{position:absolute;left:0;width:1200px;overflow:hidden}
.fill{position:absolute;inset:0}
.wordmark{display:flex;align-items:center;gap:14px;font-weight:800;line-height:1;letter-spacing:.5px}
.mark-square{border:4px solid currentColor;flex:none}

/* header */
.site-header{top:0;height:108px;display:flex;align-items:center;justify-content:space-between;padding:0 140px 0 107px}
.site-header .wordmark{font-size:19px}
.site-header .mark-square{width:52px;height:52px;border-width:5px}
.main-nav{display:flex;align-items:center;gap:34px;font-size:13px;font-weight:500;letter-spacing:.5px}
.main-nav .divider{width:2px;height:32px;background:var(--ink)}
.main-nav .social{font-weight:700;font-size:12px}

/* hero */
.hero{top:108px;height:605px;color:var(--white);text-align:center}
.hero .fill{background:linear-gradient(160deg,var(--hero-top),#8e7e6e 45%,var(--hero-bottom))}
.hero-square{position:absolute;left:555px;top:135px;width:90px;height:90px;border:6px solid var(--white)}
.hero-title{position:absolute;top:235px;width:100%;font-size:62px;font-weight:800;letter-spacing:1px}
.hero-sub{position:absolute;top:303px;width:100%;font-size:29px;font-weight:800}
.signup{position:absolute;left:193px;top:375px;width:815px;height:67px;display:flex}
.signup .field{flex:1;background:var(--white);color:var(--muted);font-size:14px;display:flex;align-items:center;padding-left:20px;gap:12px;text-align:left}
.signup .btn{width:153px;background:var(--ink);color:var(--white);font-size:15px;font-weight:800;display:flex;align-items:center;justify-content:center}
.dots{position:absolute;top:515px;left:0;width:100%;display:flex;justify-content:center;gap:14px}
.dots span{width:9px;height:9px;background:var(--white);transform:rotate(45deg)}

/* statement */
.statement{top:713px;height:380px;text-align:center}
.statement .fill{background:var(--soft)}
.statement h2{position:absolute;top:75px;width:100%;font-size:44px;font-weight:800;line-height:56px}
.statement .rule{position:absolute;left:536px;top:262px;width:128px;height:2px;background:var(--ink)}
.statement .cta{position:absolute;top:300px;width:100%;font-size:28px;font-weight:800}

/* photo sections */
.title-block{position:absolute;display:flex;align-items:center;gap:22px;color:var(--white)}
.title-block .mark-square{width:100px;height:100px;border-width:7px}
.title-block h2{font-size:52px;font-weight:800;line-height:54px}
.blurb{position:absolute;color:var(--white);font-size:13px;line-height:21px}
.who{top:1093px;height:520px}
.who .fill{background:linear-gradient(110deg,var(--who-a),#c4946a 45%,var(--who-b))}
.who .title-block{left:107px;top:172px}
.who .blurb{left:520px;top:210px;width:435px;text-align:center}
.mantra{top:1613px;height:522px}
.mantra .fill{background:linear-gradient(100deg,var(--mantra-a),#6e5568 55%,var(--mantra-b))}
.mantra .title-block{left:107px;top:170px}
.mantra .blurb{left:107px;top:307px;width:460px}
.meet{top:2135px;height:530px}
.meet .fill{background:linear-gradient(120deg,var(--meet-a),var(--meet-b) 60%,#4a423c)}
.meet .title-block{left:394px;top:100px}
.meet .blurb{left:320px;top:305px;width:560px;text-align:center}

/* armor */
.armor{top:2665px;height:595px}
.armor .title-block{left:107px;top:95px;color:var(--ink)}
.product-name{position:absolute;left:107px;top:262px;font-size:21px;font-weight:800}
.product-text{position:absolute;left:107px;top:300px;width:420px;font-size:13px;line-height:21px;color:var(--body)}
.price{position:absolute;left:107px;top:370px;font-size:36px;font-weight:400;color:var(--muted)}
.add-cart{position:absolute;left:107px;top:436px;width:145px;height:42px;border:3px solid var(--ink);font-size:12px;font-weight:800;display:flex;align-items:center;justify-content:center}
.product-image{position:absolute;left:590px;top:95px;width:390px;height:405px;background:linear-gradient(180deg,#fafafa,#e4e4e4);border-radius:6px}

/* social */
.powers{top:3260px;height:285px}
.powers .fill{background:var(--soft)}
.powers .title-block{left:107px;top:62px;color:var(--ink)}
.social-link{position:absolute;top:74px;width:140px;height:140px;display:flex;align-items:center;justify-content:center;font-size:13px;font-weight:800}
.social-link::before{content:"";position:absolute;left:22px;top:22px;width:96px;height:96px;border:5px solid var(--ink);transform:rotate(45deg)}
.social-link.pw{left:690px}
.social-link.pl{left:868px}

/* featured */
.featured{top:3545px;height:130px;display:flex;align-items:center;justify-content:center;gap:14px}
.featured .mark-square{width:30px;height:30px}
.featured h2{font-size:26px;font-weight:800}
.gallery{top:3675px;height:215px;display:flex;gap:4px}
.gallery .tile{flex:1;height:100%}
.tile.t1{background:linear-gradient(160deg,#cfc6b4,#a68a5a)}
.tile.t2{background:linear-gradient(160deg,#9aa3ab,#3f4246)}
.tile.t3{background:linear-gradient(160deg,#b9b4ae,#c68f34)}
.tile.t4{background:linear-gradient(160deg,#e6e6e6,#3a4658)}
.tile.t5{background:linear-gradient(160deg,#e0dcd8,#8a3440)}
.tile.t6{background:linear-gradient(160deg,#d8d3cc,#7c7670)}

/* footer */
.site-footer{top:3890px;height:128px;display:flex;align-items:center;justify-content:space-between;padding:0 40px 0 107px}
.site-footer .wordmark{font-size:19px}
.site-footer .mark-square{width:52px;height:52px;border-width:5px}
.site-footer small{font-size:11px;font-weight:500;letter-spacing:.3px}
</style>
</head>
<body>

<header class="section site-header">
  <div class="wordmark"><span class="mark-square"></span><span>WE ARE<br>BRIGHT<br>SPARROW</span></div>
  <nav class="main-nav">
    <span>MISSION</span><span>MANTRA</span><span>MEET BS</span><span>ARMOR</span>
    <span class="divider"></span>
    <span class="social">PAGEWAVE</span><span class="social">PICTOLANE</span>
  </nav>
</header>

<section class="section hero">
  <div class="fill" role="img" aria-label="Woman running on a mountain trail at sunset above a city"></div>
  <div class="hero-square"></div>
  <h1 class="hero-title">WE ARE BRIGHT SPARROW</h1>
  <p class="hero-sub">AND I WILL CONQUER THE WORLD</p>
  <form class="signup">
    <div class="field">
      <svg width="16" height="12" viewBox="0 0 16 12"><rect x="1" y="1" width="14" height="10" fill="none" stroke="#555" stroke-width="1.5"/><path d="M1 1l7 6 7-6" fill="none" stroke="#555" stroke-width="1.5"/></svg>
      you@example.com
    </div>
    <div class="btn">LET'S FLY</div>
  </form>
  <div class="dots"><span></span><span></span><span></span><span></span></div>
</section>

<section class="section statement">
  <div class="fill" role="img" aria-label="Light grey geometric background pattern"></div>
  <h2>WE ARE BRIGHT SPARROW IS A GLOBAL<br>EMPOWERMENT MOVEMENT ELEVATING<br>WOMEN... AND THE WORLD.</h2>
  <div class="rule"></div>
  <p class="cta">LET'S FLY</p>
</section>

<section class="section who">
  <div class="fill" role="img" aria-label="Three smiling women together in warm sunlight"></div>
  <div class="title-block"><span class="mark-square"></span><h2>WHO<br>WE<br>ARE</h2></div>
  <p class="blurb">We are a movement of women who lift one another, share stories of courage and grow bold together, one step at a time, in every city across the world today.</p>
</section>

<section class="section mantra">
  <div class="fill" role="img" aria-label="Woman raising her fist against the setting sun"></div>
  <div class="title-block"><span class="mark-square"></span><h2>OUR<br>MANTRA</h2></div>
  <p class="blurb">Our mantra is simple: rise, stand tall and speak with a clear voice. We believe every woman carries a quiet strength that can change her home, her town and beyond.</p>
</section>

<section class="section meet">
  <div class="fill" role="img" aria-label="Woman working at a laptop in a bright office"></div>
  <div class="title-block"><span class="mark-square"></span><h2>MEET<br>BRIGHT<br>SPARROWS</h2></div>
  <p class="blurb">Meet the women behind the movement, from founders and mentors to makers and dreamers. Each one brings a story of grit and grace, and each one shows what is possible when we choose to fly together with open hearts.</p>
</section>

<section class="section armor">
  <div class="title-block"><span class="mark-square"></span><h2>OUR<br>ARMOR</h2></div>
  <h3 class="product-name">BRIGHT SPARROWS T-SHIRT</h3>
  <p class="product-text">Soft cotton tee made to be worn with pride, printed with our mark and sent with love to you.</p>
  <p class="price">$39.00</p>
  <div class="add-cart">ADD TO CART</div>
  <div class="product-image" role="img" aria-label="White t-shirt printed with the Bright Sparrow name"></div>
</section>

<section class="section powers">
  <div class="fill" role="img" aria-label="Light grey geometric background pattern"></div>
  <div class="title-block"><span class="mark-square"></span><h2>SHOW OFF<br>YOUR SUPER<br>POWERS</h2></div>
  <div class="social-link pw"><span>PAGEWAVE</span></div>
  <div class="social-link pl"><span>PICTOLANE</span></div>
</section>

<section class="section featured">
  <span class="mark-square"></span><h2>FEATURED BRIGHT SPARROW</h2>
</section>

<section class="section gallery">
  <div class="tile t1" role="img" aria-label="Portrait of a featured member in a mustard top"></div>
  <div class="tile t2" role="img" aria-label="Portrait of a featured member against a grey wall"></div>
  <div class="tile t3" role="img" aria-label="Portrait of a featured member in a yellow blouse"></div>
  <div class="tile t4" role="img" aria-label="Portrait of a featured member in a navy jacket"></div>
  <div class="tile t5" role="img" aria-label="Portrait of a featured member in a burgundy top"></div>
  <div class="tile t6" role="img" aria-label="Portrait of a featured member in a striped top"></div>
</section>

<footer class="section site-footer">
  <div class="wordmark"><span class="mark-square"></span><span>WE ARE<br>BRIGHT<br>SPARROW</span></div>
  <small>©2017 COMPANY NAME | ALL RIGHTS RESERVED</small>
</footer>

</body>
</html>
```